MV Decor

There is a sample provided with the arabic text of the business card. please copy paste the same text and the same Logo (The two triangles) Just try to incorproate the Brown background attached (you are free to change the colors) Id like the colors to be mainly shades of black and red.

```html
<!DOCTYPE html>
<html lang="ar">
<head>
<meta charset="utf-8">
<title>MV Decor – Business Card</title>
<link href="https://fonts.googleapis.com/css2?family=Aref+Ruqaa:wght@400;700&family=Tajawal:wght@300;400;700&family=Roboto:wght@400&display=swap" rel="stylesheet">
<style>
  :root {
    --backdrop: #2b2b2b;
    --card-red: #c8213f;
    --card-red-light: #d93a55;
    --card-red-deep: #b81a37;
    --ink-white: #ffffff;
    --mark-dark: #232320;
  }
  html, body {
    margin: 0;
    padding: 0;
    width: 1125px;
    height: 1200px;
    overflow: hidden;
    background: var(--backdrop);
  }
  .canvas {
    position: relative;
    width: 1125px;
    height: 1200px;
  }
  .card {
    position: absolute;
    left: 171px;
    width: 826px;
    height: 472px;
    box-shadow: 0 3px 10px rgba(0,0,0,0.55);
    overflow: hidden;
  }
  .card--front { top: 106px; }
  .card--back { top: 639px; }
  .card__texture {
    position: absolute;
    inset: 0;
    background:
      radial-gradient(ellipse at 55% 35%, var(--card-red-light) 0%, rgba(217,58,85,0) 60%),
      linear-gradient(180deg, var(--card-red) 0%, var(--card-red-deep) 100%);
  }
  .brand-name {
    position: absolute;
    font-family: "Tajawal", sans-serif;
    font-weight: 700;
    color: var(--ink-white);
    letter-spacing: 1px;
    white-space: nowrap;
    direction: ltr;
    text-align: center;
    line-height: 1;
  }
  .card--front .brand-name {
    left: 140px;
    width: 210px;
    top: 208px;
    font-size: 36px;
  }
  .divider {
    position: absolute;
    left: 396px;
    top: 95px;
    width: 1px;
    height: 254px;
    background: rgba(255,255,255,0.85);
  }
  .contact {
    position: absolute;
    right: 149px;
    top: 96px;
    direction: rtl;
    text-align: right;
    color: var(--ink-white);
  }
  .contact__name {
    font-family: "Aref Ruqaa", serif;
    font-weight: 700;
    font-size: 30px;
    line-height: 1.2;
    margin: 0;
  }
  .contact__role {
    font-family: "Aref Ruqaa", serif;
    font-size: 19px;
    margin: 2px 0 0;
    line-height: 1.4;
    text-align: center;
  }
  .contact__credentials {
    list-style: none;
    margin: 26px 0 0;
    padding: 0;
    font-family: "Tajawal", sans-serif;
    font-weight: 400;
    font-size: 21px;
    line-height: 26px;
  }
  .contact__phone {
    margin-top: 26px;
    font-family: "Roboto", sans-serif;
    font-size: 21px;
    direction: ltr;
    display: flex;
    align-items: center;
    gap: 6px;
    justify-content: flex-end;
  }
  .contact__phone svg { width: 18px; height: 18px; }
  .card--back .brand-name {
    left: 122px;
    width: 255px;
    top: 218px;
    font-size: 44px;
  }
  .services {
    position: absolute;
    right: 114px;
    top: 112px;
    width: 300px;
    list-style: none;
    margin: 0;
    padding: 0;
    direction: rtl;
    font-family: "Tajawal", sans-serif;
    font-size: 25px;
    line-height: 33px;
    color: var(--ink-white);
  }
  .services__item {
    position: relative;
    text-align: right;
    padding-left: 20px;
  }
  .services__item::after {
    content: "";
    position: absolute;
    left: 0;
    top: 13px;
    width: 8px;
    height: 8px;
    border-radius: 50%;
    background: var(--mark-dark);
  }
</style>
</head>
<body>
<main class="canvas">
  <section class="card card--front" aria-label="Business card front">
    <div class="card__texture" role="img" aria-label="Red background with a soft pattern of small squares and circles"></div>
    <div class="brand-name">MV DECOR</div>
    <div class="divider"></div>
    <div class="contact">
      <p class="contact__name">المهندس / سامر نبيل الحداد</p>
      <p class="contact__role">أستاذ جامعي</p>
      <ul class="contact__credentials">
        <li>ماجستير هندسة ديكور</li>
        <li>دبلوم عالي فن تشكيلي</li>
        <li>معهد الفنون العليا (ليون)</li>
        <li>استشارات هندسية-فنية</li>
      </ul>
      <div class="contact__phone">
        <svg viewBox="0 0 24 24" aria-hidden="true"><path fill="#fff" d="M6.6 10.8c1.4 2.8 3.8 5.1 6.6 6.6l2.2-2.2c.3-.3.7-.4 1-.2 1.1.4 2.300.6 3.6.6.6 0 1 .4 1 1V20c0 .6-.4 1-1 1C10.6 21 3 13.4 3 4c0-.6.4-1 1-1h3.5c.6 0 1 .4 1 1 0 1.3.2 2.5.6 3.6.1.3 0 .7-.2 1z"/></svg>
        <span>35550142 / 66550198</span>
      </div>
    </div>
  </section>

  <section class="card card--back" aria-label="Business card back">
    <div class="card__texture" role="img" aria-label="Red background with a soft pattern of small squares and circles"></div>
    <div class="brand-name">MV DECOR</div>
    <ul class="services">
      <li class="services__item">ماجستير هندسة ديكور</li>
      <li class="services__item">دبلوم عالي فن تشكيلي</li>
      <li class="services__item">معهد الفنون العليا (ليون)</li>
      <li class="services__item">استشارات هندسية-فنية</li>
      <li class="services__item">ماجستير هندسة ديكور</li>
      <li class="services__item">دبلوم عالي فن تشكيلي</li>
      <li class="services__item">معهد الفنون العليا (ليون)</li>
      <li class="services__item">استشارات هندسية-فنية</li>
    </ul>
  </section>
</main>
</body>
</html>
```